Business Cards for a law firm

Business cards for our law firm. Use our silhoette logo and OAK PARTNERS - check our website (www.oakpartners.example)

Contact Information for Business Card

our silhouette logo, OAK PARTNERS, 800-555-0147, Dorian Pemberton, dorian@oakpartners.example

Requirements
Must have
• our silhouette logo, OAK PARTNERS, 800-555-0147, Dorian Pemberton, dorian@oakpartners.example

```html
<!DOCTYPE html>
<html lang="en">
<head>
<meta charset="utf-8">
<title>Oak Partners — Business Cards</title>
<link rel="stylesheet" href="https://fonts.googleapis.com/css2?family=Montserrat:wght@700;800&family=Roboto:wght@400&display=swap">
<style>
  :root {
    --bg: #15171c;
    --navy-deep: #14244f;
    --navy-mid: #16237a;
    --navy-bright: #1a3a8f;
    --edge: #3d63b8;
    --white: #ffffff;
    --emboss: #1b2b63;
    --figure: rgba(110, 150, 220, 0.35);
  }
  * { box-sizing: border-box; margin: 0; padding: 0; }
  html, body { width: 1200px; height: 840px; overflow: hidden; background: var(--bg); }
  .canvas {
    width: 1200px; height: 840px;
    display: flex; align-items: center; justify-content: center; gap: 40px;
  }
  .card {
    position: relative;
    width: 560px; height: 320px;
    border-radius: 22px;
    overflow: hidden;
    border: 2px solid var(--edge);
    background: linear-gradient(120deg, var(--navy-deep) 0%, var(--navy-mid) 50%, var(--navy-bright) 75%, var(--navy-mid) 100%);
    box-shadow: 0 18px 40px rgba(0,0,0,0.55);
  }

  /* Back: embossed wordmark */
  .card--back { display: flex; align-items: center; justify-content: center; gap: 14px; }
  .card--back .brand-mark { width: 30px; height: 30px; background: var(--emboss); }
  .card--back .brand-name {
    font-family: "Montserrat", sans-serif; font-weight: 700;
    font-size: 38px; letter-spacing: 2px; color: var(--emboss);
  }

  /* Front */
  .holder-name {
    position: absolute; top: 36px; right: 62px;
    font-family: "Montserrat", sans-serif; font-weight: 800;
    font-size: 21px; letter-spacing: 1.5px; color: var(--white);
  }
  .holder-bar {
    position: absolute; top: 30px; right: 30px;
    width: 10px; height: 34px; background: var(--white);
  }
  .figure-area {
    position: absolute; right: 16px; bottom: 0;
    width: 190px; height: 230px;
    border-radius: 60px 60px 0 0;
    background: linear-gradient(180deg, var(--figure), rgba(110,150,220,0.12));
  }
  .brand {
    position: absolute; left: 54px; top: 178px;
    display: flex; align-items: center; gap: 12px;
  }
  .brand .brand-mark { width: 26px; height: 26px; background: var(--white); }
  .brand .brand-name {
    font-family: "Montserrat", sans-serif; font-weight: 700;
    font-size: 34px; letter-spacing: 1px; color: var(--white);
  }
  .contacts {
    position: absolute; left: 94px; top: 228px;
    list-style: none;
    font-family: "Roboto", sans-serif; font-size: 17px; color: var(--white);
  }
  .contacts li { display: flex; align-items: center; gap: 9px; line-height: 24px; }
  .contacts svg { width: 15px; height: 15px; fill: var(--white); flex: none; }
</style>
</head>
<body>
<main class="canvas">
  <section class="card card--back" aria-label="Card back">
    <span class="brand-mark"></span>
    <span class="brand-name">OAK PARTNERS</span>
  </section>

  <section class="card card--front" aria-label="Card front">
    <p class="holder-name">DORIAN PEMBERTON</p>
    <span class="holder-bar"></span>
    <div class="figure-area" role="img" aria-label="Faint large silhouette of two standing men"></div>

    <div class="brand">
      <span class="brand-mark"></span>
      <span class="brand-name">OAK PARTNERS</span>
    </div>

    <ul class="contacts">
      <li>
        <svg viewBox="0 0 24 24" aria-hidden="true"><path d="M6.6 10.8a15.1 15.1 0 0 0 6.6 6.6l2.2-2.2c.3-.3.7-.4 1-.2 1.1.4 2.3.6 3.6.6.6 0 1 .4 1 1V20c0 .6-.4 1-1 1C10.6 21 3 13.4 3 4c0-.6.4-1 1-1h3.5c.6 0 1 .4 1 1 0 1.3.2 2.5.6 3.6.1.3 0 .7-.2 1z"/></svg>
        800-555-0147
      </li>
      <li>
        <svg viewBox="0 0 24 24" aria-hidden="true"><path d="M3 5h18v14H3zm2 2v.5l7 4.5 7-4.5V7zm0 2.8V17h14V9.8l-7 4.5z"/></svg>
        dorian@oakpartners.example
      </li>
      <li>
        <svg viewBox="0 0 24 24" aria-hidden="true"><path d="M12 2a10 10 0 1 0 0 20 10 10 0 0 0 0-20zm6.9 6h-2.9a15.7 15.7 0 0 0-1.4-3.6A8 8 0 0 1 18.9 8zM12 4c.8 1.2 1.5 2.5 1.9 4h-3.8c.4-1.5 1.1-2.8 1.9-4zM4.3 14a8 8 0 0 1 0-4h3.4a16 16 0 0 0 0 4zm.8 2h2.9c.3 1.3.8 2.5 1.4 3.6A8 8 0 0 1 5.1 16zM8 8H5.1a8 8 0 0 1 4.3-3.6C8.8 5.5 8.3 6.7 8 8zm4 12c-.8-1.2-1.5-2.5-1.9-4h3.8c-.4 1.5-1.1 2.8-1.9 4zm2.3-6H9.7a14.7 14.7 0 0 1 0-4h4.6a14.7 14.7 0 0 1 0 4zm.3 5.6c.6-1.1 1.1-2.3 1.4-3.6h2.9a8 8 0 0 1-4.3 3.6zm1.7-5.6a16 16 0 0 0 0-4h3.4a8 8 0 0 1 0 4z"/></svg>
        www.oakpartners.example
      </li>
    </ul>
  </section>
</main>
</body>
</html>
```